Briloran Clear Springs needs a new business card design (we produce and sell pure bottled water)

We need a clean modern design for our new business cards, We have an existing logo which ultimately cannot be changed, however it could be slighty improved and the colours adjusted. We have this existing logo on all of our bottles, vehicles etc.

Our company slogan is "Pure down to the last drop".
Along with our relevant company information
(Address, phone, website email etc) we will only be using names and not putting position titles for flexibilty.

We are looking for a clean, minimalist modern design.

You can view our website (if need of an update also!) to see our business.

Industry/Entity Type

Business

Contact Information for Business Card

Staff Name : XXXXXX XXXXXX
Address : 9/41 Tavenor St
Halden Rise QLD 4172
Staff Mobile Number : 04XX XXX XXX
Office Phone Number : 07 3918 2457
Staff Email Address : XXXX@brilorancleargo.com.au
Website : www.brilorancleargo.com.au

Font styles to use
Sans Serif

Colors
cee9f5
33a6d7
0492cd
0455a3
3276b5
85abd2
cedeed

Requirements
Must have
• The ability to edit and change the staff members details as we will need to edit for each respective staff member (7 in total)

```html
<!DOCTYPE html>
<html lang="en">
<head>
<meta charset="utf-8">
<title>Briloran Clear Springs – Business Card</title>
<link rel="stylesheet" href="https://fonts.googleapis.com/css2?family=Open+Sans:wght@400;600;700&display=swap">
<style>
  :root {
    --backdrop: #9b9b9b;
    --card: #050505;
    --card-sheen: #151515;
    --blue-mist: #cee9f5;
    --blue-sky: #33a6d7;
    --blue-bright: #0492cd;
    --blue-deep: #0455a3;
    --blue-mid: #3276b5;
    --blue-soft: #85abd2;
    --blue-pale: #cedeed;
  }
  * { box-sizing: border-box; margin: 0; padding: 0; }
  html, body {
    width: 1200px;
    height: 1200px;
    overflow: hidden;
    background: var(--backdrop);
  }
  .canvas {
    width: 1200px;
    height: 1200px;
    display: flex;
    align-items: center;
    justify-content: center;
  }
  .business-card {
    position: relative;
    width: 1000px;
    height: 572px;
    background: linear-gradient(160deg, var(--card-sheen) 0%, var(--card) 45%, var(--card) 100%);
    box-shadow: 0 20px 50px rgba(0,0,0,0.35);
    font-family: "Open Sans", sans-serif;
    color: var(--blue-pale);
  }
  .brand {
    position: absolute;
    left: 300px;
    top: 128px;
    display: flex;
    align-items: center;
    gap: 18px;
  }
  .brand-dot {
    width: 34px;
    height: 34px;
    border-radius: 50%;
    background: var(--blue-sky);
  }
  .brand-name {
    font-weight: 700;
    font-size: 40px;
    letter-spacing: 0.5px;
    color: var(--blue-bright);
    text-transform: uppercase;
    line-height: 1;
  }
  .slogan {
    position: absolute;
    left: 352px;
    top: 186px;
    font-size: 20px;
    font-style: italic;
    letter-spacing: 0.5px;
    color: var(--blue-soft);
  }
  .staff {
    position: absolute;
    right: 520px;
    top: 300px;
    text-align right;
    text-align: right;
  }
  .staff-name {
    font-size: 34px;
    font-weight: 600;
    color: var(--blue-sky);
    line-height: 1.15;
    margin-bottom: 10px;
  }
  .staff-address {
    font-size: 22px;
    line-height: 1.45;
  }
  .divider {
    position: absolute;
    left: 500px;
    top: 290px;
    width: 2px;
    height: 150px;
    background: var(--blue-mid);
  }
  .contact-list {
    position: absolute;
    left: 530px;
    top: 296px;
    list-style: none;
  }
  .contact-item {
    display: flex;
    align-items: center;
    gap: 16px;
    font-size: 22px;
    line-height: 1;
    margin-bottom: 18px;
  }
  .contact-icon {
    width: 22px;
    height: 22px;
    flex: none;
  }
</style>
</head>
<body>
<main class="canvas">
  <section class="business-card" aria-label="Business card front">
    <div class="brand">
      <span class="brand-dot"></span>
      <span class="brand-name">Briloran Clear Springs</span>
    </div>
    <p class="slogan">Pure down to the last drop</p>

    <div class="staff">
      <p class="staff-name">Marla Devenish</p>
      <p class="staff-address">9/41 Tavenor St Halden Rise<br>QLD 4172</p>
    </div>

    <div class="divider"></div>

    <ul class="contact-list">
      <li class="contact-item">
        <svg class="contact-icon" viewBox="0 0 22 22" aria-hidden="true">
          <rect width="22" height="22" fill="#0455a3"/>
          <path d="M7 5 h3 l1 4 -2 1 c1 2 2 3 4 4 l1 -2 4 1 v3 c-7 0 -11 -4 -11 -11z" fill="#cee9f5"/>
        </svg>
        <span>0739182457</span>
      </li>
      <li class="contact-item">
        <svg class="contact-icon" viewBox="0 0 22 22" aria-hidden="true">
          <rect width="22" height="22" fill="#0455a3"/>
          <rect x="5" y="7" width="12" height="8" fill="none" stroke="#cee9f5" stroke-width="1.6"/>
          <path d="M5 7 l6 5 6 -5" fill="none" stroke="#cee9f5" stroke-width="1.6"/>
        </svg>
        <span>marla@brilorancleargo.com</span>
      </li>
      <li class="contact-item">
        <svg class="contact-icon" viewBox="0 0 22 22" aria-hidden="true">
          <rect width="22" height="22" fill="#0455a3"/>
          <circle cx="11" cy="11" r="6" fill="none" stroke="#cee9f5" stroke-width="1.6"/>
          <path d="M5 11 h12 M11 5 c-3 3 -3 9 0 12 M11 5 c3 3 3 9 0 12" fill="none" stroke="#cee9f5" stroke-width="1.3"/>
        </svg>
        <span>www.brilorancleargo.com</span>
      </li>
    </ul>
  </section>
</main>
</body>
</html>
```